Automotive component supplier needs a business card design

We need a business card design for our company called Velran Global Components Ltd based in the UK. We are a supplier of interior and exterior components to premium car manufacturers such as Corvel Ashby, Hadley Fenn, Marquist and Tavarelli. We would like to see a modern business card design that uses the colour blue.

Target Market(s)

Premium automotive car manufacturers.

Industry/Entity Type

Automotive

Contact Information for Business Card

Company Name : Velran Global Components Limited
Address: 17 Marlow Yard, Upper Heath, Warwick, CV31 8QL, United Kingdom
Web Address : www.velrancomponents-example.co.uk

Font styles to use
Other font styles liked:
• Helvetica

Colors
3176b5
0255a3
85acd3
cfdeed
cee9f5
85cae6
34a6d7
0692cd
9bcb3c

Requirements
Must have
• Clear company logo and a mixture of blue colours.
Nice to have
• A high quality modern image.
Should not have
• Multiple colours.

```html
<!DOCTYPE html>
<html lang="en">
<head>
<meta charset="utf-8">
<title>Velran Global Components – Business Card</title>
<link href="https://fonts.googleapis.com/css2?family=Lato:wght@400;700;900&display=swap" rel="stylesheet">
<style>
  :root {
    --brand-blue: #0a8bd0;
    --deep-blue: #0692cd;
    --accent-green: #9bcb3c;
    --ink: #2b2b2b;
    --rule: #555555;
    --paper: #ffffff;
    --backdrop: #3a3b3d;
  }
  * { box-sizing: border-box; margin: 0; padding: 0; }
  html, body { width: 1200px; height: 800px; overflow: hidden; }
  body {
    background: var(--backdrop);
    font-family: "Lato", Helvetica, Arial, sans-serif;
    position: relative;
  }
  .card {
    position: absolute;
    top: 251px;
    width: 520px;
    height: 297px;
    border-radius: 3px;
    overflow: hidden;
    box-shadow: 0 10px 28px rgba(0,0,0,.45);
  }

  /* Back of card */
  .card-back { left: 50px; background: var(--brand-blue); color: var(--paper); }
  .card-back .wordmark {
    position: absolute; left: 0; right: 0; top: 88px; text-align: center;
  }
  .card-back .website {
    position: absolute; left: 0; right: 0; bottom: 34px; text-align: center;
    font-size: 13px; letter-spacing: 1.6px;
  }

  /* Wordmark */
  .wordmark-name {
    display: block; font-weight: 900; font-size: 58px; line-height: 1;
    letter-spacing: 2px; text-transform: uppercase;
  }
  .wordmark-sub {
    display: block; font-weight: 900; font-size: 14.5px; letter-spacing: 3.4px;
    text-transform: uppercase; margin-top: 6px;
  }

  /* Front of card */
  .card-front { left: 630px; background: var(--paper); color: var(--ink); }
  .card-front .wordmark {
    position: absolute; left: 38px; top: 40px; color: var(--brand-blue);
  }
  .card-front .wordmark-name { font-size: 50px; }
  .card-front .wordmark-sub { font-size: 12.5px; letter-spacing: 2.9px; }

  .holder { position: absolute; right: 40px; top: 120px; text-align: right; }
  .holder-name { color: var(--brand-blue); font-weight: 700; font-size: 21px; }
  .holder-role { font-size: 13px; margin-top: 2px; }
  .divider {
    position: absolute; left: 24px; right: 40px; top: 172px;
    height: 1.4px; background: var(--rule);
  }

  .contact-list {
    position: absolute; left: 26px; bottom: 30px; list-style: none;
    font-size: 14px; line-height: 19.5px;
  }
  .contact-list li { display: flex; align-items: center; gap: 9px; }
  .contact-list svg { width: 12px; height: 12px; fill: var(--brand-blue); flex: none; }

  .address {
    position: absolute; right: 40px; bottom: 52px; text-align: right;
    font-size: 13.5px; line-height: 17px; font-style: normal;
  }

  .edge-band { position: absolute; left: 0; bottom: 0; width: 520px; height: 10px; }
</style>
</head>
<body>

<section class="card card-back" aria-label="Business card, back">
  <div class="wordmark">
    <span class="wordmark-name">Velran</span>
    <span class="wordmark-sub">Global Components</span>
  </div>
  <p class="website">www.velrancomponents-example.co.uk</p>
</section>

<section class="card card-front" aria-label="Business card, front">
  <div class="wordmark">
    <span class="wordmark-name">Velran</span>
    <span class="wordmark-sub">Global Components</span>
  </div>

  <div class="holder">
    <p class="holder-name">Edwin Harlowe</p>
    <p class="holder-role">Manager</p>
  </div>
  <div class="divider"></div>

  <ul class="contact-list">
    <li>
      <svg viewBox="0 0 24 24" aria-hidden="true"><path d="M6.6 10.8a15.1 15.1 0 0 0 6.6 6.6l2.2-2.2c.3-.3.7-.4 1-.2 1.1.4 2.3.6 3.6.6.6 0 1 .4 1 1V20c0 .6-.4 1-1 1A17 17 0 0 1 3 4c0-.6.4-1 1-1h3.5c.6 0 1 .4 1 1 0 1.3.2 2.5.6 3.6.1.3 0 .7-.2 1z"/></svg>
      0192 655 0148
    </li>
    <li>
      <svg viewBox="0 0 24 24" aria-hidden="true"><path d="M7 1h10a2 2 0 0 1 2 2v18a2 2 0 0 1-2 2H7a2 2 0 0 1-2-2V3a2 2 0 0 1 2-2zm0 3v14h10V4zm5 15.5a1.2 1.2 0 1 0 0 2.4 1.2 1.2 0 0 0 0-2.4z"/></svg>
      0192 655 0149
    </li>
    <li>
      <svg viewBox="0 0 24 24" aria-hidden="true"><path d="M2 5h20v14H2zm2 2v.5l8 5 8-5V7zm0 2.8V17h16V9.8l-8 5z"/></svg>
      info@velrancomponents-example.co.uk
    </li>
    <li>
      <svg viewBox="0 0 24 24" aria-hidden="true"><path d="M12 2a10 10 0 1 0 0 20 10 10 0 0 0 0-20zm6.9 6h-2.9a15 15 0 0 0-1.4-3.6A8 8 0 0 1 18.9 8zM12 4c.8 1.2 1.5 2.5 1.9 4h-3.8c.4-1.5 1.1-2.8 1.9-4zM4.3 14a8 8 0 0 1 0-4h3.4a16 16 0 0 0 0 4zm.8 2h2.9c.3 1.3.8 2.5 1.4 3.6A8 8 0 0 1 5.1 16zM8 8H5.1a8 8 0 0 1 4.3-3.6C8.8 5.5 8.3 6.7 8 8zm4 12c-.8-1.2-1.5-2.5-1.9-4h3.8c-.4 1.5-1.1 2.8-1.9 4zm2.3-6H9.7a14 14 0 0 1 0-4h4.6a14 14 0 0 1 0 4zm.3 5.6c.6-1.1 1.1-2.3 1.4-3.6h2.9a8 8 0 0 1-4.3 3.6zm1.7-5.6a16 16 0 0 0 0-4h3.4a8 8 0 0 1 0 4z"/></svg>
      www.velrancomponents-example.co.uk
    </li>
  </ul>

  <address class="address">
    17 Marlow Yard, Upper Heath<br>
    Warwick, CV31 8QL<br>
    United Kingdom
  </address>

  <svg class="edge-band" viewBox="0 0 520 10" preserveAspectRatio="none" aria-hidden="true">
    <polygon points="0,4 345,4 340,10 0,10" fill="var(--accent-green)"/>
    <polygon points="350,0 520,0 520,10 342,10" fill="var(--brand-blue)"/>
  </svg>
</section>

</body>
</html>
```